Equipment Finance Specialist I work with companies who need the funds to buy their equipment

I would like a business card that stands out on the shelves. I want to be able to hand it to someone and say WOW. This card should have my logo.
You can put color into it I am very open on design and color

What my company does is we deal with dealerships that sell equipment such as Dump Trucks garbage trucks tractors trailers. Customers get referred to us and depending on their time in business we will ask for the following items

Companies that have been in business for more than two years we have a credit application program up to 250K . With this program we need the following items Credit application filled out(which is what I would like to be able for the customer to click on my website to get.) as well as three current month bank statements.

Deals over 250k we will need the following items

2 years business tax returns
2 years personal tax returns
Profit & Loss statement
Personal Financial Statement

what we do
100% FINANCING
SEASONAL PAYMENTS
LOAN BALLOON PAYMENTS
TRAC LEASING
LOW-INTEREST REFINANCING RATES
DEBT CONSOLIDATION

We specialize in creative financing solutions and offer a variety of reliable, flexible and expandable lending choices.

Target Market(s)

Trucking Companies

Industry/Entity Type

Trucking Company

Contact Information for Business Card

* $250,000 Application only Program
* Loans from $30,000 to 5,000,000
* Competitive Interest Rates

Font styles to use
Serif
Sans Serif

Colors

Designer to choose colors to be used in the design.

Requirements
Must have
• On the back of the card.
• * $250,000 Application only Program
• * Loans from $30,000 to 5,000,000
• My name, email, website. address
• * Competitive Interest Rates
• * 100% Financing
Nice to have
• I want my logo to pop on the card
• My logo is the great one I would like to use
Should not have
• I am up for your creativity as well

```html
<!DOCTYPE html>
<html lang="en">
<head>
<meta charset="utf-8">
<title>Ridgeline Funding — Business Card</title>
<link href="https://fonts.googleapis.com/css2?family=Roboto:wght@400;700;900&display=swap" rel="stylesheet">
<style>
  :root {
    --navy: #0b2468;
    --red: #c8102e;
    --grey-text: #444a55;
    --divider: #c9ccd2;
    --backdrop: #e4e4e4;
    --white: #ffffff;
  }
  * { margin: 0; padding: 0; box-sizing: border-box; }
  html, body { width: 1125px; height: 1200px; overflow: hidden; }
  body {
    background: var(--backdrop);
    font-family: "Roboto", Arial, sans-serif;
    position: relative;
  }
  .card {
    position: absolute;
    left: 171px;
    width: 826px;
    height: 471px;
    border-radius: 28px;
    border: 10px solid;
  }
  .card--front { top: 105px; background: var(--white); border-color: var(--navy); }
  .card--back { top: 640px; background: var(--navy); border-color: var(--white); }

  .brand {
    position: absolute;
    display: flex;
    align-items: center;
    font-weight: 900;
    text-transform: uppercase;
    letter-spacing: 1px;
    line-height: 1;
    white-space: nowrap;
  }
  .brand__dot { border-radius: 50%; flex: none; }
  .card--front .brand { left: 48px; top: 205px; gap: 14px; color: var(--navy); font-size: 29px; }
  .card--front .brand__dot { width: 44px; height: 44px; background: var(--navy); }
  .card--back .brand { left: 0; right: 0; justify-content: center; top: 185px; gap: 16px; color: var(--white); font-size: 50px; }
  .card--back .brand__dot { width: 70px; height: 70px; background: var(--white); }

  .divider {
    position: absolute;
    left: 460px;
    top: 122px;
    width: 2px;
    height: 215px;
    background: var(--divider);
  }
  .contact { position: absolute; left: 499px; top: 118px; }
  .contact__name { color: var(--navy); font-weight: 700; font-size: 30px; letter-spacing: 0.5px; line-height: 1.05; }
  .contact__role { color: var(--red); font-weight: 700; font-size: 20px; margin-top: 2px; }
  .contact__address { color: var(--grey-text); font-size: 19.5px; line-height: 25px; margin-top: 20px; }
  .contact__list { list-style: none; margin-top: 10px; }
  .contact__list li {
    display: flex; align-items: center; gap: 12px;
    color: var(--grey-text); font-size: 19.5px; line-height: 26px;
  }
  .contact__list svg { width: 18px; height: 18px; flex: none; fill: var(--navy); }

  .offers {
    position: absolute;
    left: 0; right: 0; top: 369px;
    text-align: center;
    color: var(--white);
    font-size: 19.5px;
    line-height: 27px;
  }
  .offers .sep { font-size: 14px; vertical-align: 2px; margin: 0 2px; }
</style>
</head>
<body>

<section class="card card--front" aria-label="Card front">
  <div class="brand"><span class="brand__dot"></span>Ridgeline Funding</div>
  <div class="divider"></div>
  <div class="contact">
    <p class="contact__name">DANIEL REYES</p>
    <p class="contact__role">CEO/FOUNDER</p>
    <p class="contact__address">2140 Cedar Ridge Road<br>Boise, Idaho 83702</p>
    <ul class="contact__list">
      <li>
        <svg viewBox="0 0 24 24" aria-hidden="true"><path d="M6.6 10.8a15.1 15.1 0 0 0 6.6 6.6l2.2-2.2c.3-.3.7-.4 1-.2 1.1.4 2.3.6 3.6.6.6 0 1 .4 1 1V20c0 .6-.4 1-1 1A17 17 0 0 1 3 4c0-.6.4-1 1-1h3.5c.6 0 1 .4 1 1 0 1.3.2 2.5.6 3.6.1.3 0 .7-.2 1z"/></svg>
        208 555 0143
      </li>
      <li>
        <svg viewBox="0 0 24 24" aria-hidden="true"><path d="M2 5h20v14H2zm2 2.2V17h16V7.2l-8 6.1z M4.5 7h15L12 12.7z"/></svg>
        daniel@ridgelinefunding.com
      </li>
      <li>
        <svg viewBox="0 0 24 24" aria-hidden="true"><circle cx="12" cy="12" r="10"/><path d="M2 12h20M12 2c3 3 3 17 0 20M12 2c-3 3-3 17 0 20" fill="none" stroke="#ffffff" stroke-width="1.4"/></svg>
        www.ridgelinefunding.com
      </li>
    </ul>
  </div>
</section>

<section class="card card--back" aria-label="Card back">
  <div class="brand"><span class="brand__dot"></span>Ridgeline Funding</div>
  <div class="offers">
    <p>$250,000 Application only Program <span class="sep">●</span> Loans from $30,000 to 5,000,000</p>
    <p>Competitive Interest Rates <span class="sep">●</span> 100% Financing</p>
  </div>
</section>

</body>
</html>
```